New Business Card Design Project

Need a design that will create an impact / strong impression towards our clients for our business. We are in the lighting business and we do lighting retrofits for large commercial to industrial clientele.

Target Market(s)

Lighting Industry

Industry/Entity Type

Business

Font styles to use
Other font styles liked:
• we would like to use the font on our logo, not sure what it is though..

Requirements
Must have
• Our logo.
Nice to have
• We are open to suggestions that have to do with lighting.

```html
<!DOCTYPE html>
<html lang="en">
<head>
<meta charset="utf-8">
<title>Corvane Retrofit Co. – Business Card</title>
<link href="https://fonts.googleapis.com/css2?family=Montserrat:wght@400;600;800&display=swap" rel="stylesheet">
<style>
  :root {
    --page-bg: #e6e8e6;
    --card-white: #ffffff;
    --green-deep: #0f4a1c;
    --green-mid: #1f6e2e;
    --green-bright: #2fa043;
    --green-text: #237a35;
    --ink-dark: #163d1e;
    --ink-grey: #444a46;
    --on-green: #ffffff;
  }
  * { box-sizing: border-box; margin: 0; padding: 0; }
  html, body { width: 1200px; height: 900px; overflow: hidden; }
  body {
    background: var(--page-bg);
    font-family: "Montserrat", sans-serif;
    display: flex;
    flex-direction: column;
    align-items: center;
    justify-content: center;
    gap: 36px;
  }
  .card {
    position: relative;
    width: 700px;
    height: 400px;
    background: var(--card-white);
    box-shadow: 0 6px 22px rgba(0,0,0,0.18);
    overflow: hidden;
  }

  /* Front */
  .card-front { display: flex; align-items: center; justify-content: center; }
  .brand-mark { display: flex; align-items: center; gap: 14px; }
  .brand-mark .brand-square {
    width: 26px; height: 26px; background: var(--green-bright);
  }
  .brand-mark .brand-name {
    font-weight: 800; font-size: 38px; color: var(--green-mid);
    letter-spacing: 0.5px; white-space: nowrap;
  }
  .brand-rule {
    display: block; height: 2px; background: var(--green-mid);
    margin-top: 8px;
  }
  .brand-block { display: flex; flex-direction: column; }

  /* Back */
  .card-back .brand-block { position: absolute; left: 42px; top: 90px; }
  .card-back .brand-mark .brand-square { width: 20px; height: 20px; }
  .card-back .brand-mark .brand-name { font-size: 30px; }

  .person {
    position: absolute; right: 42px; top: 42px; text-align: left;
  }
  .person-name { font-weight: 800; font-size: 20px; color: var(--ink-dark); white-space: nowrap; }
  .person-role { font-weight: 400; font-size: 17px; color: var(--green-text); margin-top: 2px; }

  .green-band {
    position: absolute; left: 0; right: 0; top: 165px; height: 180px;
    background: linear-gradient(100deg, var(--green-mid) 0%, var(--green-deep) 55%, var(--green-mid) 100%);
  }
  .contact {
    position: absolute; left: 42px; bottom: 14px;
    color: var(--on-green); font-size: 15px; line-height: 1.3;
  }
  .contact-address { margin-bottom: 6px; }
  .contact-row { display: flex; align-items: center; gap: 10px; }
  .contact-row svg { width: 13px; height: 13px; fill: var(--on-green); flex: none; }

  .web-strip {
    position: absolute; left: 0; right: 0; bottom: 0; height: 55px;
    display: flex; align-items: center; padding-left: 42px;
    border-top: 3px solid var(--green-bright);
  }
  .web-address { font-weight: 600; font-size: 13px; letter-spacing: 0.6px; color: var(--ink-grey); text-transform: uppercase; }
</style>
</head>
<body>

  <section class="card card-front">
    <div class="brand-block">
      <div class="brand-mark">
        <span class="brand-square"></span>
        <span class="brand-name">Corvane Retrofit Co.</span>
      </div>
      <span class="brand-rule"></span>
    </div>
  </section>

  <section class="card card-back">
    <div class="person">
      <div class="person-name">RENNA CALLOWAY</div>
      <div class="person-role">CEO/FOUNDER</div>
    </div>

    <div class="green-band">
      <div class="contact">
        <div class="contact-address">1420 Lantern Way<br>Harbor City, Alaska 30012</div>
        <div class="contact-row">
          <svg viewBox="0 0 24 24"><path d="M6.6 10.8a15 15 0 0 0 6.6 6.6l2.2-2.2a1 1 0 0 1 1-.25 11.4 11.4 0 0 0 3.6.57 1 1 0 0 1 1 1V20a1 1 0 0 1-1 1A17 17 0 0 1 3 4a1 1 0 0 1 1-1h3.5a1 1 0 0 1 1 1c0 1.25.2 2.45.57 3.57a1 1 0 0 1-.25 1z"/></svg>
          <span>555 210 4471</span>
        </div>
        <div class="contact-row">
          <svg viewBox="0 0 24 24"><path d="M7 1h10a2 2 0 0 1 2 2v18a2 2 0 0 1-2 2H7a2 2 0 0 1-2-2V3a2 2 0 0 1 2-2zm0 3v14h10V4zm5 15.5a1.2 1.2 0 1 0 0 2.4 1.2 1.2 0 0 0 0-2.4z"/></svg>
          <span>555 386 9052</span>
        </div>
        <div class="contact-row">
          <svg viewBox="0 0 24 24"><path d="M6 2h10v5H6zM4 8h16a2 2 0 0 1 2 2v8h-4v4H6v-4H2v-8a2 2 0 0 1 2-2zm4 8v4h8v-4z"/></svg>
          <span>555 742 1183</span>
        </div>
        <div class="contact-row">
          <svg viewBox="0 0 24 24"><path d="M2 5h20v14H2zm2 2v.5l8 5 8-5V7zm0 2.8V17h16V9.8l-8 5z"/></svg>
          <span>hello@corvaneretrofit.com</span>
        </div>
      </div>
    </div>

    <div class="brand-block">
      <div class="brand-mark">
        <span class="brand-square"></span>
        <span class="brand-name">Corvane Retrofit Co.</span>
      </div>
      <span class="brand-rule"></span>
    </div>

    <div class="web-strip">
      <span class="web-address">www.corvaneretrofit.com</span>
    </div>
  </section>

</body>
</html>
```